Web design for financial services

A modern web design of financial services (brokerage firm)
Req.s and technology tags :
- Very mobile friendly.
- One paged with some inner pages.
- Animated sticky header .
- Member login area for e-trade.
- Support RTL language.
- HTML & CSS.

The logo will be Home link
• MPTR :
WHO WE ARE
Content :
i) Board of Directors
ii) Mission Statement
iii) Corporate Values
iv) Regulations
• Financial Services :
WHAT WE DO
Content:
i) Electronic trading
ii) Trading desk
iii) Institutional
iv) Investors Education
• News
• Market Tools
• Forms---- opens new page
• Careers---- opens new page
• Contact Us----opens new page

The website is :
http://www.mptr-doha-example.com/

The logo need some changes to be more modern and impressively , but with keeping same structure .

Some related websites :
https://www.lv-bourse.example/

financial market

Financial Service

Coded - Design and coding required

2 page

• same fonts of http://www.kwdholdings.example/

• - Very mobile friendly.
• - One paged with some inner pages.
• - Animated sticky header .
• - Member login area for e-trade.
• - Support RTL language.
• - HTML & CSS.
• Slider , some Qatari theme,
• i like the video inside the home page
• ex :http://www.kwdholdings.example/

```html
<!DOCTYPE html>
<html lang="en">
<head>
<meta charset="utf-8">
<title>MPTR — Careers</title>
<link rel="stylesheet" href="https://fonts.googleapis.com/css2?family=Open+Sans:ital,wght@0,400;0,600;0,700;0,800;1,600;1,700&display=swap">
<style>
  :root{
    --brand-red:#8e1b1b;
    --ink:#1d1d1d;
    --body:#3a3a3a;
    --muted:#cfcfcf;
    --white:#ffffff;
    --footer:#000000;
    --hero-dark:#2a211d;
    --hero-warm:#6b5140;
  }
  *{margin:0;padding:0;box-sizing:border-box}
  html,body{width:1200px;height:2687px;overflow:hidden;background:var(--white)}
  body{font-family:"Open Sans",Arial,sans-serif;color:var(--ink);position:relative}
  .abs{position:absolute}

  /* header */
  .site-header{position:absolute;left:0;top:0;width:1200px;height:120px;background:var(--white)}
  .brand{position:absolute;left:75px;top:38px;display:flex;align-items:center;gap:14px;text-decoration:none}
  .brand-mark{width:44px;height:44px;background:var(--brand-red)}
  .brand-name{font-size:42px;font-weight:800;color:var(--ink);letter-spacing:1px;line-height:1}
  .etrade-btn{position:absolute;left:926px;top:27px;width:102px;height:26px;background:var(--brand-red);color:var(--white);
    font-size:10px;font-weight:700;display:flex;align-items:center;justify-content:center;gap:6px;border-radius:2px}
  .lang-select{position:absolute;left:1037px;top:27px;width:86px;height:26px;border:1px solid #9a9a9a;border-radius:2px;
    font-size:9px;font-weight:600;display:flex;align-items:center;justify-content:center;gap:5px}
  .lang-flag{width:12px;height:8px;background:linear-gradient(#c8102e 0 50%,#1a3a8a 50%)}
  .main-nav{position:absolute;top:81px;left:0;width:1200px;height:20px}
  .main-nav a{position:absolute;font-size:12px;font-weight:700;color:var(--ink);text-decoration:none;text-transform:uppercase}
  .main-nav a.is-active{color:var(--brand-red)}

  /* hero */
  .hero{position:absolute;left:0;top:120px;width:1200px;height:543px;
    background:linear-gradient(120deg,var(--hero-dark) 0%,var(--hero-warm) 40%,#4a3b35 70%,#7b7472 100%)}
  .hero-shade{position:absolute;inset:0;background:rgba(20,14,12,.35)}
  .hero-title{position:absolute;left:0;top:182px;width:1200px;text-align:center;color:var(--white);font-size:58px;font-weight:700;letter-spacing:1px}
  .hero-cut{position:absolute;left:0;top:120px}

  /* intro */
  .section-label{position:absolute;left:161px;top:700px;font-size:15px;font-weight:700;color:var(--brand-red)}
  .section-label::after{content:"";position:absolute;left:0;top:32px;width:48px;height:4px;background:var(--ink)}
  .intro-rule{position:absolute;left:340px;top:698px;width:1px;height:291px;background:var(--muted)}
  .intro-text{position:absolute;left:381px;top:700px;width:658px;font-size:11px;line-height:21.6px;color:var(--body)}
  .cv-button{position:absolute;left:381px;top:947px;width:247px;height:44px;border:1px solid #9a9a9a;border-radius:2px;
    display:flex;align-items:center;justify-content:center;font-size:14px;font-weight:600;color:var(--brand-red)}
  .divider{position:absolute;left:161px;top:1071px;width:878px;height:1px;background:#d9d9d9}

  /* careers list */
  .list-title{position:absolute;left:161px;top:1112px;font-size:22px;font-weight:700;color:var(--brand-red)}
  .job{position:absolute;width:272px}
  .job-city{font-size:15px;font-weight:600;color:var(--ink);line-height:20px}
  .job-title{margin-top:10px;font-size:15px;font-weight:700;color:var(--ink);line-height:24px}
  .job-desc{margin-top:8px;font-size:10.5px;line-height:20.5px;color:var(--body)}
  .job-date{margin-top:12px;font-size:13px;font-weight:700;font-style:italic;color:var(--brand-red)}

  /* skyline + footer */
  .skyline{position:absolute;left:0;top:2104px;width:1200px;height:328px;
    background:linear-gradient(180deg,rgba(255,255,255,0) 0%,#e4c3bd 25%,#b86a5f 65%,#8e3d33 100%)}
  .site-footer{position:absolute;left:0;top:2432px;width:1200px;height:255px;background:var(--footer);color:var(--white)}
  .footer-brand{position:absolute;left:0;top:48px;width:1200px;display:flex;justify-content:center;align-items:center;gap:10px}
  .footer-brand .brand-mark{width:30px;height:30px;background:var(--white)}
  .footer-brand .brand-name{font-size:28px;color:var(--white)}
  .footer-nav{position:absolute;left:0;top:126px;width:1200px;text-align:center;font-size:13px;font-weight:700;word-spacing:2px}
  .footer-nav span{margin:0 10px}
  .copyright{position:absolute;left:0;top:159px;width:1200px;text-align:center;font-size:10px;color:#e5e5e5}
  .social{position:absolute;left:0;top:190px;width:1200px;display:flex;justify-content:center;gap:10px}
  .social i{display:block;width:27px;height:27px;border:1.5px solid var(--white);border-radius:50%}
</style>
</head>
<body>

<header class="site-header">
  <a class="brand" href="#"><span class="brand-mark"></span><span class="brand-name">MPTR</span></a>
  <div class="etrade-btn">
    <svg width="10" height="10" viewBox="0 0 10 10"><rect x="1" y="1" width="8" height="8" fill="none" stroke="#fff" stroke-width="1.2"/><path d="M3 5h5M6 3l2 2-2 2" fill="none" stroke="#fff" stroke-width="1.2"/></svg>
    MPTR E-TRADE
  </div>
  <div class="lang-select"><span class="lang-flag"></span>ENGLISH
    <svg width="7" height="5" viewBox="0 0 7 5"><path d="M1 1l2.5 2.5L6 1" fill="none" stroke="#333" stroke-width="1.2"/></svg>
  </div>
  <nav class="main-nav">
    <a style="left:507px">MPTR</a>
    <a style="left:566px">Financial Service</a>
    <a style="left:709px">News</a>
    <a style="left:777px">Market Tool</a>
    <a style="left:894px">Forms</a>
    <a class="is-active" style="left:967px">Careers</a>
    <a style="left:1051px">Contact Us</a>
  </nav>
</header>

<section class="hero" role="img" aria-label="Photo of a person reviewing financial charts at a desk with a laptop">
  <div class="hero-shade"></div>
  <h1 class="hero-title">CAREERS</h1>
</section>
<svg class="abs hero-cut" width="1200" height="543" viewBox="0 0 1200 543" aria-hidden="true">
  <polygon points="0,498 537,403 1200,543 0,543" fill="#ffffff"/>
</svg>

<h2 class="section-label">CAREERS</h2>
<div class="intro-rule"></div>
<p class="intro-text">Sed ut perspiciatis unde omnis iste natus error sit voluptat em accusantium dolore mque laudlorantium, totam remape riam, eaque ipsa quae ab illo inventore veritatis et quasi arc hite locto beatae vitae dictasnt explic abo enim iloreps​am vol uptatemloia voluptas sit aspe rnatur aut odit auhite cto bea tae vitae lodictasnt explic abo enim iloreps​am vol uptateloia voluptas sit aspe rnatur aut odit ahite cto beatae vitae dictst explic abo enim iloreps​am vol uptatemloia voluptas sit aspe rnatur aut odit auhite cto bea taipsa quae ab illo inventore veritatis et quasi arc hite locto beatae vitae dictasnt explic abo enim iloreps​am vol uptatemloia voluptas sit aspe rnatur aut odit auhite cto bea tae vitae lodictasnt explic abo enim iloreps​am vol uptateloia voluptas sit aspe rnatur aut odit ahite cto beatae vitae dictst explic abo enim iloreps​am vol uptatemloia voluptas sit aspe rnatur aut odit auhite cto bea taeipsa quae ab illo inventore veritatis et quasi arc hite locto beatae vitae dictasnt explic abo enim iloreps​am vol uptatemloia voluptas.dictst explic abo enim iloreps​am vol uptatemloia voluptas sit aspe rnatur aut odit auhite cto bea taeipsa quae ab illo inventore veritatis et quasi arc hite locto beatae vitae dictasnt explic abo enim iloreps​am vol uptatemloia voluptas.</p>
<div class="cv-button">Send CVs to xxx@mptr-doha-example.com</div>
<div class="divider"></div>

<h2 class="list-title">CAREERS AT MPTR</h2>

<article class="job" style="left:161px;top:1198px"><p class="job-city">New York</p><h3 class="job-title">Sed ut perspiciatis unpers piciatis ndeptatemerspiciatis unde</h3><p class="job-desc">Sed ut perspiciatis unde omnis iste natus errsit vupat em accusantium dolore mque laudlorantium, totam remape ria m, eaque ipsa quae ab illo inventore verit atis et quasi arc hite cto beatae vitae dictasnt explibo enim iloreps​am vol uptat emloia voluptas</p><p class="job-date">----- 25 February, 2017</p></article>
<article class="job" style="left:462px;top:1198px"><p class="job-city">New York</p><h3 class="job-title">Sed ut perspiciatis unpers piciatis ndeptatemerspiciatis unde</h3><p class="job-desc">Sed ut perspiciatis unde omnis iste natus errsit vupat em accusantium dolore mque laudlorantium, totam remape ria m, eaque ipsa quae ab illo inventore verit atis et quasi arc hite cto beatae vitae dictasnt explibo enim iloreps​am vol uptat emloia voluptas</p><p class="job-date">----- 25 February, 2017</p></article>
<article class="job" style="left:777px;top:1198px"><p class="job-city">New York</p><h3 class="job-title">Sed ut perspiciatis unpers piciatis ndeptatemerspiciatis unde</h3><p class="job-desc">Sed ut perspiciatis unde omnis iste natus errsit vupat em accusantium dolore mque laudlorantium, totam remape ria m, eaque ipsa quae ab illo inventore verit atis et quasi arc hite cto beatae vitae dictasnt explibo enim iloreps​am vol uptat emloia voluptas</p><p class="job-date">----- 25 February, 2017</p></article>

<article class="job" style="left:161px;top:1476px"><p class="job-city">New York</p><h3 class="job-title">Sed ut perspiciatis unpers piciatis ndeptatemerspiciatis unde</h3><p class="job-desc">Sed ut perspiciatis unde omnis iste natus errsit vupat em accusantium dolore mque laudlorantium, totam remape ria m, eaque ipsa quae ab illo inventore verit atis et quasi arc hite cto beatae vitae dictasnt explibo enim iloreps​am vol uptat emloia voluptas</p><p class="job-date">----- 25 February, 2017</p></article>
<article class="job" style="left:462px;top:1476px"><p class="job-city">New York</p><h3 class="job-title">Sed ut perspiciatis unpers piciatis ndeptatemerspiciatis unde</h3><p class="job-desc">Sed ut perspiciatis unde omnis iste natus errsit vupat em accusantium dolore mque laudlorantium, totam remape ria m, eaque ipsa quae ab illo inventore verit atis et quasi arc hite cto beatae vitae dictasnt explibo enim iloreps​am vol uptat emloia voluptas</p><p class="job-date">----- 25 February, 2017</p></article>
<article class="job" style="left:777px;top:1476px"><p class="job-city">New York</p><h3 class="job-title">Sed ut perspiciatis unpers piciatis ndeptatemerspiciatis unde</h3><p class="job-desc">Sed ut perspiciatis unde omnis iste natus errsit vupat em accusantium dolore mque laudlorantium, totam remape ria m, eaque ipsa quae ab illo inventore verit atis et quasi arc hite cto beatae vitae dictasnt explibo enim iloreps​am vol uptat emloia voluptas</p><p class="job-date">----- 25 February, 2017</p></article>

<article class="job" style="left:161px;top:1753px"><p class="job-city">New York</p><h3 class="job-title">Sed ut perspiciatis unpers piciatis ndeptatemerspiciatis unde</h3><p class="job-desc">Sed ut perspiciatis unde omnis iste natus errsit vupat em accusantium dolore mque laudlorantium, totam remape ria m, eaque ipsa quae ab illo inventore verit atis et quasi arc hite cto beatae vitae dictasnt explibo enim iloreps​am vol uptat emloia voluptas</p><p class="job-date">----- 25 February, 2017</p></article>
<article class="job" style="left:462px;top:1753px"><p class="job-city">New York</p><h3 class="job-title">Sed ut perspiciatis unpers piciatis ndeptatemerspiciatis unde</h3><p class="job-desc">Sed ut perspiciatis unde omnis iste natus errsit vupat em accusantium dolore mque laudlorantium, totam remape ria m, eaque ipsa quae ab illo inventore verit atis et quasi arc hite cto beatae vitae dictasnt explibo enim iloreps​am vol uptat emloia voluptas</p><p class="job-date">----- 25 February, 2017</p></article>
<article class="job" style="left:777px;top:1753px"><p class="job-city">New York</p><h3 class="job-title">Sed ut perspiciatis unpers piciatis ndeptatemerspiciatis unde</h3><p class="job-desc">Sed ut perspiciatis unde omnis iste natus errsit vupat em accusantium dolore mque laudlorantium, totam remape ria m, eaque ipsa quae ab illo inventore verit atis et quasi arc hite cto beatae vitae dictasnt explibo enim iloreps​am vol uptat emloia voluptas</p><p class="job-date">----- 25 February, 2017</p></article>

<div class="skyline" role="img" aria-label="Illustrated Doha city skyline in red and pink tones"></div>

<footer class="site-footer">
  <div class="footer-brand"><span class="brand-mark"></span><span class="brand-name">MPTR</span></div>
  <div class="footer-nav">MPTR<span>|</span>FINACIAL SERVICE<span>|</span>NEWS<span>|</span>MARKET TOOL<span>|</span>CAREERS<span>|</span>CONTACT US</div>
  <p class="copyright">©2017. All Rights Reserved | MPTR Qatar | Copyright, Legal and Privacy Statement.Disclaimers and Legal Information</p>
  <div class="social"><i></i><i></i><i></i><i></i><i></i></div>
</footer>

</body>
</html>
```